Business Card For Halvenmoor Financial Consulting

Hi, I would like a business card designed. Bold, modern.
Please use the same design as the logo. I have also attached the website design to see the overall theme.
Wordmark Font
Color: Hex: #01AEF7

```html
<!DOCTYPE html>
<html lang="en">
<head>
<meta charset="UTF-8">
<title>Halvenmoor Financial Consulting – Business Card</title>
<link href="https://fonts.googleapis.com/css2?family=Poppins:ital,wght@0,400;0,600;0,700;1,400&display=swap" rel="stylesheet">
<style>
  :root {
    --brand-blue: #01AEF7;
    --card-black: #161616;
    --card-shade: #1f1f1f;
    --page-bg: #2a2a2a;
    --ink-white: #f2f2f2;
  }
  * { margin: 0; padding: 0; box-sizing: border-box; }
  html, body { width: 1200px; height: 900px; overflow: hidden; }
  body {
    background: var(--page-bg);
    font-family: "Poppins", sans-serif;
    display: flex;
    flex-direction: column;
    align-items: center;
    justify-content: center;
    gap: 36px;
  }
  .card {
    position: relative;
    width: 700px;
    height: 400px;
    background: var(--card-black);
    border-bottom: 4px solid var(--brand-blue);
    overflow: hidden;
    box-shadow: 0 10px 30px rgba(0,0,0,.45);
  }
  /* Front */
  .brand {
    position: absolute;
    top: 42px; left: 48px;
    display: flex; align-items: center; gap: 14px;
  }
  .brand-square { width: 30px; height: 30px; background: var(--brand-blue); }
  .brand-name {
    color: var(--ink-white);
    font-weight: 600;
    font-size: 19px;
    letter-spacing: 2px;
    text-transform: uppercase;
    line-height: 1.2;
  }
  .address {
    position: absolute;
    top: 140px; left: 48px;
    color: var(--ink-white);
    font-size: 16px;
    line-height: 1.45;
  }
  .contact-list {
    position: absolute;
    top: 210px; left: 48px;
    list-style: none;
    color: var(--ink-white);
    font-size: 16px;
    line-height: 1.6;
  }
  .contact-list li { display: flex; align-items: center; gap: 10px; }
  .contact-list svg { width: 13px; height: 13px; fill: var(--brand-blue); flex: none; }
  .person {
    position: absolute;
    top: 120px; right: 60px;
    text-align: right;
  }
  .person-name {
    color: var(--brand-blue);
    font-weight: 700;
    font-size: 24px;
    text-transform: uppercase;
    letter-spacing: .5px;
  }
  .person-title { color: var(--ink-white); font-size: 17px; font-style: italic; }
  .edge-tab {
    position: absolute;
    right: 0; top: 178px;
    width: 14px; height: 38px;
    background: var(--brand-blue);
  }
  .corner-decor {
    position: absolute;
    right: 0; bottom: 0;
    width: 330px; height: 210px;
    background: linear-gradient(135deg, var(--card-black) 0%, var(--card-shade) 55%, #262626 100%);
  }
  /* Back */
  .back-pattern {
    position: absolute; inset: 0;
    background: linear-gradient(135deg, #151515 0%, #1c1c1c 50%, #141414 100%);
  }
  .back-brand {
    position: absolute;
    right: 48px; bottom: 44px;
    display: flex; align-items: center; gap: 12px;
  }
  .back-brand .brand-name { color: var(--brand-blue); font-size: 17px; }
</style>
</head>
<body>
  <section class="card card-front">
    <div class="brand">
      <span class="brand-square"></span>
      <span class="brand-name">Halvenmoor Financial Consulting</span>
    </div>
    <p class="address">18420 Cove Harbor Drive<br>Laguna Bay CA 92600</p>
    <ul class="contact-list">
      <li><svg viewBox="0 0 16 16"><path d="M3 1l3 3-2 2c1 2 3 4 5 5l2-2 3 3-2 3C6 15 1 10 0 3z"/></svg>555-240-6187</li>
      <li><svg viewBox="0 0 16 16"><path d="M0 3h16v2L8 10 0 5zM0 7l8 5 8-5v7H0z"/></svg>info@HalvenmoorConsulting.com</li>
      <li><svg viewBox="0 0 16 16"><circle cx="8" cy="8" r="8"/></svg>www.HalvenmoorConsulting.com</li>
    </ul>
    <div class="person">
      <p class="person-name">Marcus Trevell</p>
      <p class="person-title">President</p>
    </div>
    <span class="edge-tab"></span>
    <div class="corner-decor" role="img" aria-label="Large faint brand emblem in dark grey tones"></div>
  </section>

  <section class="card card-back">
    <div class="back-pattern" role="img" aria-label="Tonal repeating brand emblem pattern in dark grey"></div>
    <div class="back-brand">
      <span class="brand-square"></span>
      <span class="brand-name">Halvenmoor</span>
    </div>
  </section>
</body>
</html>
```